Jolly Paws Business Card Update

I have a business card which I love. I want to keep the same logo, colours, font and style. I want to upgrade the scripting and remove some elements and add others.
On the front side under Services - remove the existing wording and insert - Providing individual coaching strategies to create happy, healthy and social canine companions
Under Denise Carvell amend the current wording to read: Qualified in Dog Behavioural Training, Natural Animal Healthcare and Animal Health Science
On the reverse side to remove the web address.

```html
<!DOCTYPE html>
<html lang="en">
<head>
<meta charset="utf-8">
<title>Jolly Paws Business Card</title>
<link href="https://fonts.googleapis.com/css2?family=Arimo:wght@400;700&family=Open+Sans:wght@400;600&display=swap" rel="stylesheet">
<style>
  :root {
    --bg: #2b2b2c;
    --front-top: #0a93cc;
    --front-bottom: #2b3380;
    --navy: #283b8e;
    --paper: #f1f1f2;
    --red-dark: #5e1c1f;
    --red: #d21f27;
    --blue-left: #24418f;
    --blue-right: #0b8ccb;
    --cream: #eee8d6;
    --ink: #1b1b1b;
    --white: #ffffff;
    --light: #e8eef7;
  }
  * { margin: 0; padding: 0; box-sizing: border-box; }
  html, body { width: 1200px; height: 1138px; overflow: hidden; background: var(--bg); }
  .canvas { position: relative; width: 1200px; height: 1138px; }
  .card {
    position: absolute; border-radius: 16px; overflow: hidden;
    box-shadow: 0 4px 10px rgba(0,0,0,0.45);
  }
  .card-front {
    left: 274px; top: 186px; width: 623px; height: 376px;
    background: linear-gradient(180deg, var(--front-top) 0%, #1978bd 45%, var(--front-bottom) 100%);
    text-align: center; font-family: 'Arimo', Arial, sans-serif; color: var(--white);
  }
  .front-mark {
    position: absolute; left: 236px; top: 74px; width: 150px; height: 150px;
    border-radius: 50%; background: var(--cream);
  }
  .brand-name {
    position: absolute; left: 0; right: 0; top: 222px;
    font-size: 40px; font-weight: 400; letter-spacing: 1px; color: var(--light);
  }
  .tagline {
    position: absolute; left: 0; right: 0; top: 270px;
    font-size: 20px; color: var(--light);
  }
  .card-back {
    left: 276px; top: 608px; width: 618px; height: 374px;
    background: var(--paper);
    font-family: 'Open Sans', Arial, sans-serif;
  }
  .person-name {
    position: absolute; left: 22px; top: 34px;
    font-size: 26px; font-weight: 600; color: var(--navy); letter-spacing: -0.3px;
  }
  .qualifications {
    position: absolute; left: 22px; top: 69px;
    font-size: 14.5px; line-height: 20px; color: var(--navy);
  }
  .contact-band {
    position: absolute; left: 0; right: 0; top: 136px; height: 66px;
    background: linear-gradient(90deg, var(--red-dark) 0%, #a31c23 40%, var(--red) 62%, #8a1d21 78%, var(--red-dark) 100%);
    color: var(--white); font-size: 15.5px;
  }
  .contact-line { position: absolute; left: 22px; display: flex; align-items: center; gap: 10px; }
  .contact-line.first { top: 11px; }
  .contact-line.second { top: 34px; }
  .contact-line svg { width: 13px; height: 15px; }
  .contact-line .spacer { width: 8px; }
  .services-band {
    position: absolute; left: 0; right: 0; top: 202px; height: 102px;
    background: linear-gradient(90deg, var(--blue-left) 0%, #1d5aa5 60%, var(--blue-right) 100%);
    color: var(--white); font-family: 'Arimo', Arial, sans-serif;
  }
  .services-title { position: absolute; left: 22px; top: 20px; font-size: 18px; font-weight: 700; }
  .services-text { position: absolute; left: 22px; top: 47px; font-size: 15.5px; line-height: 18px; }
  .back-mark {
    position: absolute; left: 381px; top: 105px; width: 218px; height: 218px;
    border-radius: 50%; background: var(--red);
    display: flex; align-items: center; justify-content: center;
  }
  .back-mark span {
    font-family: 'Arimo', Arial, sans-serif; font-size: 26px; font-weight: 700; color: var(--cream);
  }
  .mission {
    position: absolute; left: 22px; top: 330px;
    font-family: 'Arimo', Arial, sans-serif; font-size: 16px; color: var(--ink);
  }
</style>
</head>
<body>
<div class="canvas">
  <section class="card card-front">
    <div class="front-mark"></div>
    <div class="brand-name">JOLLY PAWS</div>
    <div class="tagline">HAPPY DOGS, HAPPY OWNERS</div>
  </section>

  <section class="card card-back">
    <div class="person-name">Denise Carvell</div>
    <div class="qualifications">Qualified in Dog Behavioural Training,<br>Natural Animal Healthcare &amp; Animal Health Science</div>

    <div class="contact-band">
      <div class="contact-line first">
        <svg viewBox="0 0 13 15" aria-hidden="true"><rect x="2" y="0.5" width="9" height="14" rx="1" fill="none" stroke="#fff" stroke-width="1.2"/><rect x="3.5" y="2" width="6" height="4" fill="#fff"/><g fill="#fff"><rect x="3.5" y="7.5" width="1.5" height="1.2"/><rect x="6" y="7.5" width="1.5" height="1.2"/><rect x="8.5" y="7.5" width="1" height="1.2"/><rect x="3.5" y="10" width="1.5" height="1.2"/><rect x="6" y="10" width="1.5" height="1.2"/><rect x="8.5" y="10" width="1" height="1.2"/></g></svg>
        <span>0400 127 356</span>
        <span class="spacer"></span>
        <svg viewBox="0 0 15 11" style="width:15px;height:11px" aria-hidden="true"><rect x="0" y="0" width="15" height="11" fill="#fff"/><path d="M0 0 L7.5 6 L15 0" fill="none" stroke="#a31c23" stroke-width="1.4"/></svg>
        <span>jollypaws1@example.com</span>
      </div>
      <div class="contact-line second">
        <svg viewBox="0 0 13 13" style="width:13px;height:13px" aria-hidden="true"><g fill="none" stroke="#fff" stroke-width="1"><circle cx="6.5" cy="6.5" r="5.8"/><ellipse cx="6.5" cy="6.5" rx="2.6" ry="5.8"/><line x1="0.7" y1="6.5" x2="12.3" y2="6.5"/><line x1="1.5" y1="3.6" x2="11.5" y2="3.6"/><line x1="1.5" y1="9.4" x2="11.5" y2="9.4"/></g></svg>
        <span>www.jollypaws1.com</span>
      </div>
    </div>

    <div class="services-band">
      <div class="services-title">SERVICES</div>
      <div class="services-text">Providing individual coaching strategies to create<br>happy, healthy and social canine companions</div>
    </div>

    <div class="back-mark"><span>Jolly Paws</span></div>

    <div class="mission">Promoting communication and connection between dogs and their families</div>
  </section>
</div>
</body>
</html>
```